full stationary design for a modern sleek design company

we are a design company that does modern minimalistic interior design works as well as other design services for high end clients.
we need a full stationary design including and not limited to (double sided business card, letter head, envelopes, documents folder...etc) that reflects the modern style design we do.
sleek modern and minimalistic is the requirements.
Updates

please use the latest attached files as there was a slight modification on the logo Added Wednesday, March 1, 2017

minor update on the logo files in JPG and PSD has been updated kindly follow the new attachments. Added Thursday, March 2, 2017

Target Market(s)

modern minimalist clients

Industry/Entity Type

Design Agency

Requirements
Must have
• the logo
Nice to have
• i like the colors in the colored 3D logo attached
Should not have
• too many colors

```html
<!DOCTYPE html>
<html lang="en">
<head>
<meta charset="utf-8">
<title>Linea Studio — Business Card</title>
<link rel="stylesheet" href="https://fonts.googleapis.com/css2?family=Open+Sans:wght@400;600&display=swap">
<style>
  :root {
    --page-bg: #3a3a3a;
    --card-front: #fafafa;
    --card-back: #2e2e2e;
    --ink: #2b2b2b;
    --ink-soft: #444444;
    --accent: #f28c1c;
    --band: #2d2d2d;
    --white: #ffffff;
  }
  * { margin: 0; padding: 0; box-sizing: border-box; }
  html, body { width: 1200px; height: 750px; overflow: hidden; }
  body {
    background: var(--page-bg);
    font-family: "Open Sans", sans-serif;
    position: relative;
  }
  .card {
    position: absolute;
    top: 228px;
    width: 461px;
    height: 262px;
    border-radius: 12px;
    overflow: hidden;
  }
  .card--front { left: 124px; background: var(--card-front); }
  .card--back { left: 618px; background: var(--card-back); }

  .wordmark {
    position: absolute;
    display: flex;
    align-items: center;
    gap: 8px;
    font-weight: 600;
    letter-spacing: 2px;
    white-space: nowrap;
  }
  .wordmark__square { display: block; background: currentColor; }
  .card--front .wordmark {
    right: 28px; top: 42px;
    font-size: 22px; color: var(--ink);
  }
  .card--front .wordmark__square { width: 20px; height: 20px; }
  .card--back .wordmark {
    left: 0; right: 0; top: 114px;
    justify-content: center;
    font-size: 27px; color: var(--accent);
  }
  .card--back .wordmark__square { width: 26px; height: 26px; }

  .person { position: absolute; left: 22px; top: 126px; right: 29px; }
  .person__name {
    font-size: 16px; font-weight: 600; color: var(--accent);
    line-height: 20px;
  }
  .person__role-row { display: flex; align-items: center; }
  .person__role { font-size: 12.5px; color: var(--ink); line-height: 16px; }
  .person__rule { flex: 1; height: 1px; background: var(--ink); margin-top: 3px; }

  .contacts {
    position: absolute; left: 23px; top: 171px;
    list-style: none; font-size: 12px; color: var(--ink-soft);
  }
  .contacts li { display: flex; align-items: center; gap: 6px; height: 17.5px; }
  .contacts svg { width: 12px; height: 12px; fill: var(--accent); }

  .address {
    position: absolute; right: 28px; top: 189px;
    font-size: 12px; color: var(--ink-soft);
    text-align: right; font-style: normal; line-height: 17.5px;
  }

  .band {
    position: absolute; left: 0; right: 0; top: 234px; height: 19px;
    background: var(--band);
    display: flex; align-items: center; justify-content: space-between;
    padding: 0 28px 0 23px;
  }
  .band__web { font-size: 12px; color: var(--white); letter-spacing: .6px; }
  .band__mark { font-size: 11px; font-weight: 600; color: var(--accent); letter-spacing: 1px; }
</style>
</head>
<body>
  <section class="card card--front" aria-label="Business card front">
    <div class="wordmark"><span class="wordmark__square"></span>LINEA STUDIO</div>

    <div class="person">
      <p class="person__name">NOAH BRENNER</p>
      <div class="person__role-row">
        <span class="person__role">CEO&amp;Founder</span>
        <span class="person__rule"></span>
      </div>
    </div>

    <ul class="contacts">
      <li>
        <svg viewBox="0 0 24 24" aria-hidden="true"><path d="M6.6 10.8a15.1 15.1 0 0 0 6.6 6.6l2.2-2.2a1 1 0 0 1 1-.25 11.4 11.4 0 0 0 3.6.57 1 1 0 0 1 1 1V20a1 1 0 0 1-1 1A17 17 0 0 1 3 4a1 1 0 0 1 1-1h3.5a1 1 0 0 1 1 1c0 1.25.2 2.45.57 3.6a1 1 0 0 1-.25 1z"/></svg>
        (555) 214 7730
      </li>
      <li>
        <svg viewBox="0 0 24 24" aria-hidden="true"><path d="M7 1h10a2 2 0 0 1 2 2v18a2 2 0 0 1-2 2H7a2 2 0 0 1-2-2V3a2 2 0 0 1 2-2zm0 3v14h10V4z"/></svg>
        (555) 381 0462
      </li>
      <li>
        <svg viewBox="0 0 24 24" aria-hidden="true"><path d="M2 5h20v14H2zm2 2v.5l8 5 8-5V7l-8 5z"/></svg>
        noah@lineastudio.com
      </li>
    </ul>

    <address class="address">214 Alder Court<br>Fairview, Oregon 97024</address>

    <div class="band">
      <span class="band__web">www.lineastudio.com</span>
      <span class="band__mark">LINEA</span>
    </div>
  </section>

  <section class="card card--back" aria-label="Business card back">
    <div class="wordmark"><span class="wordmark__square"></span>LINEA STUDIO</div>
  </section>
</body>
</html>
```